Harborline Renewal Business Card Design

Professional and clean design. The design colors should flow with the logo. Two-sided card with the website on the back which is:

www.HarborlineRenewal.example.

"Specializing in Water Damage Restoration"

On the front I need the name, email, phone, and logo.

Name: Darnell Quisby
Email: Darnell@HarborlineRenewal.example
Phone: 555-318-2046 for now

I only have the Preview and Thumbnail right now but should have the source files uploaded within a day or two.

Target Market(s)

Flood victims, home owners with water damage from busted pipes etc...

Industry/Entity Type

Business

Contact Information for Business Card

Name: Darnell Quisby

Font styles to use
Serif
Sans Serif

Requirements
Must have
• Business Card Details Info

```html
<!DOCTYPE html>
<html lang="en">
<head>
<meta charset="utf-8">
<title>Harborline Renewal Business Card</title>
<link href="https://fonts.googleapis.com/css2?family=Cinzel:wght@500&family=Arimo:wght@400;700&display=swap" rel="stylesheet">
<style>
  :root {
    --stage: #ecebe8;
    --card-grey: #a8a8a8;
    --card-white: #ffffff;
    --brand-blue: #2fa3dc;
    --text-grey: #4d4d4d;
    --on-grey: #ffffff;
  }
  html, body { margin: 0; padding: 0; overflow: hidden; }
  body {
    width: 1200px; height: 950px;
    background: var(--stage);
    position: relative;
    font-family: "Arimo", Arial, sans-serif;
  }
  .card {
    position: absolute;
    width: 600px; height: 343px;
    box-shadow: 0 6px 18px rgba(0,0,0,.18);
    box-sizing: border-box;
    overflow: hidden;
  }
  .card--back { left: 80px; top: 80px; background: var(--card-grey); color: var(--on-grey); }
  .card--front { left: 520px; top: 500px; background: var(--card-white); }

  .wordmark {
    font-family: "Cinzel", Georgia, serif;
    font-weight: 500;
    letter-spacing: 0.5px;
    white-space: nowrap;
    display: flex; align-items: center; gap: 12px;
    margin: 0;
  }
  .wordmark__dot { width: 30px; height: 30px; border-radius: 50%; flex: none; }

  .card--back .wordmark { position: absolute; left: 0; right: 0; top: 128px; justify-content: center; font-size: 30px; color: var(--on-grey); }
  .card--back .wordmark__dot { background: var(--on-grey); }
  .tagline { position: absolute; left: 0; right: 0; top: 196px; margin: 0; text-align: center; font-size: 16px; }

  .tab {
    position: absolute; left: 262px; top: 0;
    width: 64px; height: 72px;
    background: var(--brand-blue);
    border-radius: 0 0 32px 32px;
    display: flex; align-items: flex-end; justify-content: center;
    padding-bottom: 8px; box-sizing: border-box;
  }
  .tab__circle { width: 48px; height: 48px; border-radius: 50%; background: var(--card-white); }
  .card--front .wordmark { position: absolute; right: 40px; top: 92px; font-size: 28px; color: var(--brand-blue); }

  .contact { position: absolute; left: 40px; bottom: 38px; color: var(--text-grey); }
  .contact__name { color: var(--brand-blue); font-weight: 700; font-size: 20px; margin: 0 0 12px; }
  .contact__list { list-style: none; margin: 0; padding: 0; font-size: 14.5px; line-height: 21px; }
  .contact__list li { display: flex; align-items: center; gap: 8px; }
  .contact__list svg { width: 13px; height: 13px; fill: var(--brand-blue); flex: none; }
</style>
</head>
<body>
  <section class="card card--back" aria-label="Card back">
    <p class="wordmark"><span class="wordmark__dot"></span>Harborline Renewal</p>
    <p class="tagline">Specializing in Water Damage Restoration</p>
  </section>

  <section class="card card--front" aria-label="Card front">
    <div class="tab"><span class="tab__circle"></span></div>
    <p class="wordmark">Harborline Renewal</p>
    <div class="contact">
      <p class="contact__name">Darnell Quisby</p>
      <ul class="contact__list">
        <li><svg viewBox="0 0 24 24" aria-hidden="true"><path d="M6.6 10.8a15 15 0 0 0 6.6 6.6l2.2-2.2a1 1 0 0 1 1-.25 11.4 11.4 0 0 0 3.6.57 1 1 0 0 1 1 1V20a1 1 0 0 1-1 1A17 17 0 0 1 3 4a1 1 0 0 1 1-1h3.5a1 1 0 0 1 1 1c0 1.25.2 2.45.57 3.6a1 1 0 0 1-.25 1z"/></svg>555-318-2046 for now</li>
        <li><svg viewBox="0 0 24 24" aria-hidden="true"><path d="M2 5h20v14H2zm2 2v.5l8 5 8-5V7l-8 5z"/></svg>Darnell@HarborlineRenewal.example</li>
        <li><svg viewBox="0 0 24 24" aria-hidden="true"><path d="M12 2a7 7 0 0 0-7 7c0 5 7 13 7 13s7-8 7-13a7 7 0 0 0-7-7zm0 9.5A2.5 2.5 0 1 1 12 6.5a2.5 2.5 0 0 1 0 5z"/></svg>HarborlineRenewal.example</li>
      </ul>
    </div>
  </section>
</body>
</html>
```